Flowmark Engineering Business Card

our company has just rebranded and taken on a new logo design. We now need to update our business cards with the new logo. This is also an opportunity to reformat and modernize our look. We are an engineering company so the look needs to be formal and professional yet it should look modern. Have a look at our current card and the new card should have the same information.

Target Market(s)

Engineering firms, government, mining companies

Industry/Entity Type

Mechanical Engineering

Contact Information for Business Card

see example attached

Requirements
Must have
• look professional and modern
Should not have
• should not include the office locations 'Brisbane, Sydney and Kuala Lumpur'
• you will find this on the example but it should not be included in these versions. please remove from your submissions and resubmit

```html
<!DOCTYPE html>
<html lang="en">
<head>
<meta charset="utf-8">
<title>Flowmark Engineering Business Card</title>
<link rel="stylesheet" href="https://fonts.googleapis.com/css2?family=Saira+Semi+Condensed:wght@400;600&display=swap">
<style>
  :root {
    --bg: #d9d9d9;
    --card: #ffffff;
    --brand: #3b40ad;
    --ink: #2b2b2b;
    --muted: #6b6b6b;
    --rule: #3a3a3a;
  }
  * { box-sizing: border-box; margin: 0; padding: 0; }
  html, body { width: 1200px; height: 947px; overflow: hidden; }
  body {
    background: var(--bg);
    font-family: "Saira Semi Condensed", sans-serif;
    display: flex;
    align-items: center;
    justify-content: center;
    gap: 90px;
  }
  .card {
    width: 400px;
    height: 660px;
    background: var(--card);
    border-radius: 28px;
    position: relative;
    box-shadow: 0 14px 30px rgba(0,0,0,0.18);
  }
  /* Back */
  .back-brand {
    position: absolute;
    top: 50%; left: 50%;
    transform: translate(-50%, -50%);
    display: flex; flex-direction: column; align-items: center; gap: 18px;
  }
  .brand-dot {
    width: 96px; height: 96px; border-radius: 50%;
    border: 8px solid var(--brand);
  }
  .brand-name {
    color: var(--brand); font-weight: 600; font-size: 26px; letter-spacing: 4px;
  }
  .social {
    position: absolute; bottom: 26px; right: 28px;
    display: flex; gap: 22px;
  }
  .social-item {
    display: flex; align-items: center; gap: 6px;
    font-size: 14px; color: var(--muted);
  }
  .social-item .square { width: 16px; height: 16px; background: var(--brand); }
  /* Front */
  .front { padding: 60px 44px; }
  .front-brand { display: flex; align-items: center; gap: 16px; }
  .front-brand .brand-dot { width: 64px; height: 64px; border-width: 6px; }
  .front-brand .brand-name { font-size: 30px; letter-spacing: 3px; line-height: 1.05; }
  .front-brand .brand-name small {
    display: block; font-size: 30px; letter-spacing: 3px;
  }
  .contact { margin-top: 70px; display: flex; flex-direction: column; gap: 44px; }
  .row { display: flex; align-items: center; gap: 16px; }
  .row svg { width: 40px; height: 40px; flex: none; fill: var(--brand); }
  .bar { width: 4px; height: 50px; background: var(--rule); flex: none; }
  .lines { font-size: 19px; color: var(--ink); line-height: 1.3; letter-spacing: 0.5px; }
  .person-name {
    font-size: 26px; font-weight: 600; color: var(--brand); letter-spacing: 1px; line-height: 1.1;
  }
  .person-title { font-size: 16px; color: var(--muted); }
</style>
</head>
<body>
  <section class="card back">
    <div class="back-brand">
      <div class="brand-dot"></div>
      <div class="brand-name">FLOWMARK</div>
    </div>
    <div class="social">
      <span class="social-item"><span class="square"></span>/flowmark</span>
      <span class="social-item"><span class="square"></span>@flowmark</span>
    </div>
  </section>

  <section class="card front">
    <div class="front-brand">
      <div class="brand-dot"></div>
      <div class="brand-name">FLOWMARK<small>ENGINEERING</small></div>
    </div>
    <div class="contact">
      <div class="row">
        <svg viewBox="0 0 40 40" aria-hidden="true"><circle cx="20" cy="12" r="8"/><path d="M4 38c0-9 7-15 16-15s16 6 16 15z"/></svg>
        <span class="bar"></span>
        <div class="lines">
          <div class="person-name">DANIEL MERCER</div>
          <div class="person-title">Managing Director</div>
        </div>
      </div>
      <div class="row">
        <svg viewBox="0 0 40 40" aria-hidden="true"><path d="M20 2C12 2 7 8 7 15c0 10 13 23 13 23s13-13 13-23C33 8 28 2 20 2zm0 19a6 6 0 1 1 0-12 6 6 0 0 1 0 12z"/></svg>
        <span class="bar"></span>
        <div class="lines">214 9th floor Tower<br>Harbour Road NTX</div>
      </div>
      <div class="row">
        <svg viewBox="0 0 40 40" aria-hidden="true"><path fill-rule="evenodd" d="M20 2a18 18 0 1 0 0 36 18 18 0 0 0 0-36zm-2 3.2c-2.6 3-4.2 7.6-4.5 12.8H5.2A15 15 0 0 1 18 5.2zm4 0A15 15 0 0 1 34.8 18h-8.3c-.3-5.2-1.9-9.8-4.5-12.8zM16.5 18c.3-5 2-9.2 3.5-11.4 1.5 2.2 3.2 6.4 3.5 11.4zm-11.3 4h8.3c.3 5.2 1.9 9.8 4.5 12.8A15 15 0 0 1 5.2 22zm11.3 0h7c-.3 5-2 9.2-3.5 11.4-1.5-2.2-3.2-6.4-3.5-11.4zm10 0h8.3A15 15 0 0 1 22 34.8c2.6-3 4.2-7.6 4.5-12.8z"/></svg>
        <span class="bar"></span>
        <div class="lines">021 555 0148<br>daniel@flowmark.com<br>flowmarkeng.com</div>
      </div>
    </div>
  </section>
</body>
</html>
```